Pebblebrook Plots - Online-only garden installation company

Online-only garden installation company. Our demographic is middle aged / suburban women, and we anticipate Facebook driving traffic to this website, as well as referrals from garden centers. The website must be very simple in design and function.

All orders will be placed through the website, including size of garden (3 options), location in yard, payment, and scheduling of installation date.

The website should employ a 3 step process:

Step 1: Select garden size. Either an 4' X 4', 8' X 4', or 12' X 4'.

Step 2: Select a location. We would like to use google maps to look up a US address, then "drag and drop" one of the garden sizes from step 1 to the location the customer would like us to install the garden at their home.

Step 3: Pick an installation date and pay. Using an online calendar the customer will pick a date, and then pay for the installation via credit card.

The website will be linked to an email account, PebblebrookPlots@mailvale.com to inform us of orders placed.

Target Market(s)

Our demographic is middle aged / suburban women, and we anticipate Facebook driving traffic to this website, as well as referrals from garden centers.

Industry/Entity Type

Coding

Number of Pages Required

Requirements
Must have
• Scheduling and payment options.

```html
<!DOCTYPE html>
<html lang="en">
<head>
<meta charset="utf-8">
<title>Pebblebrook Plots</title>
<link rel="stylesheet" href="https://fonts.googleapis.com/css2?family=Bitter:wght@700&family=Merriweather:wght@400&family=Raleway:wght@300&family=Roboto:wght@400&family=Tinos&display=swap">
<style>
:root{
  --orange:#ee5a2a;
  --orange-dark:#d9400f;
  --green:#3a7f37;
  --green-btn:#3b8a3a;
  --ink:#222;
  --footer-dark:#25301c;
  --white:#fff;
}
*{margin:0;padding:0;box-sizing:border-box}
html,body{width:1021px;height:1200px;overflow:hidden;background:var(--white);font-family:'Roboto',sans-serif;color:var(--ink)}
.page{position:relative;width:1021px;height:1200px}
.abs{position:absolute}

.header{top:0;left:0;width:1021px;height:113px;background:var(--white)}
.logo-tab{top:0;left:80px;width:152px;height:152px;z-index:3}
.brand{top:82px;left:80px;width:152px;text-align:center;font-family:'Merriweather',serif;font-size:14px;letter-spacing:.5px;color:#2b2b2b;z-index:4}
.brand-mark{top:20px;left:140px;width:32px;height:32px;border-radius:50%;background:var(--green);z-index:4}
.helpline{top:30px;left:623px;font-size:10.5px;color:var(--orange)}
.phone-icon{top:22px;left:788px}
.phone-num{top:25px;left:825px;font-size:19px;color:#222}
.nav{top:75px;left:532px;display:flex;font-family:'Merriweather',serif;font-size:12.5px;color:#222}
.nav a{color:inherit;text-decoration:none}
.nav .active{color:var(--orange)}
.nav .sep{color:#bbb;margin:0 25px}

.hero{top:113px;left:0;width:1021px;height:398px;background:linear-gradient(100deg,#b49564 0%,#8f7448 30%,#4c6a32 55%,#3d6a2a 75%,#7c8a4c 100%)}
.hero-arrow{top:318px}
.caption{top:432px;left:88px;width:933px;height:59px;background:rgba(60,55,45,.6);color:#fff;font-family:'Raleway',sans-serif;font-weight:300;font-size:26px;text-align:center;line-height:59px}

.section-title{top:546px;left:0;width:1021px;text-align:center;font-family:'Bitter',serif;font-weight:700;font-size:25px;color:#222}
.title-rule{top:588px;left:472px;width:78px;height:2px;background:var(--green)}

.card{top:614px;width:279px;height:257px;border:1px solid #d8d8d8;background:#fff}
.card-photo{position:absolute;top:16px;left:40px;width:198px;height:150px;border-radius:8px;background:radial-gradient(ellipse at 50% 40%,#4f8a36 0%,#6f9a44 40%,#c9a56a 75%,#fff 100%)}
.card-text{position:absolute;top:194px;left:0;width:100%;text-align:center;font-size:13.5px;color:#222}
.card-bar{position:absolute;left:-1px;bottom:-1px;width:279px;height:30px;background:var(--orange);display:flex;align-items:center;color:#fff}
.size{font-size:13px;margin-left:9px;width:90px}
.price{margin-left:8px;width:68px;height:22px;border-radius:3px;background:var(--orange-dark);font-weight:700;font-size:12.5px;text-align:center;line-height:22px}
.buy{margin-left:6px;width:90px;height:22px;border-radius:3px;background:var(--orange-dark);font-size:11px;display:flex;align-items:center;justify-content:center;gap:5px}

.footer{top:934px;left:0;width:1021px;height:228px;border-radius:30px 30px 0 0;background:linear-gradient(90deg,#25311e 0%,#2b3a22 45%,#4a3b28 70%,#6b4a2a 100%)}
.f-head{font-family:'Tinos',serif;font-size:15.5px;color:#fff}
.f-rule{height:1px;background:rgba(255,255,255,.18)}
.f-body{font-size:11.2px;line-height:18.4px;color:#fff}
.f-line{font-size:11.8px;color:#fff;display:flex;align-items:center;gap:8px}
.social{top:1108px;left:327px;display:flex;gap:6px}
.social span{width:24px;height:24px;border-radius:2px}
.input{top:1041px;left:556px;width:168px;height:21px;background:#fff;border-radius:3px;font-size:10px;color:#444;padding-left:6px;line-height:21px}
.subscribe{top:1076px;left:557px;width:99px;height:23px;background:var(--green-btn);color:#fff;font-size:12.5px;text-align:center;line-height:23px;border-radius:2px}
.f-brand{top:1040px;left:770px;width:170px;text-align:center;font-family:'Merriweather',serif;font-size:18px;color:rgba(255,255,255,.35)}

.bottom{top:1162px;left:0;width:1021px;height:38px;background:var(--green);color:#fff;font-family:'Tinos',serif;font-size:12px}
.copy{top:12px;left:71px}
.accept{top:12px;left:785px}
.cards{top:9px;left:852px;display:flex;gap:6px}
.cards span{height:19px;padding:0 4px;background:#fff;color:var(--green);font-family:'Roboto',sans-serif;font-size:8.5px;line-height:19px;border-radius:2px}
</style>
</head>
<body>
<div class="page">

  <header class="abs header"></header>
  <svg class="abs logo-tab" width="152" height="152" viewBox="0 0 152 152"><polygon points="0,0 152,0 152,113 76,152 0,113" fill="#fff"/></svg>
  <div class="abs brand-mark"></div>
  <div class="abs brand">PEBBLEBROOK PLOTS</div>

  <div class="abs helpline">Need any help? Call Us Anytime</div>
  <svg class="abs phone-icon" width="28" height="28" viewBox="0 0 24 24"><path fill="#3a7f37" d="M6.6 10.8a15.1 15.1 0 0 0 6.6 6.6l2.2-2.2a1 1 0 0 1 1-.25 11.4 11.4 0 0 0 3.6.57 1 1 0 0 1 1 1V20a1 1 0 0 1-1 1A17 17 0 0 1 3 4a1 1 0 0 1 1-1h3.5a1 1 0 0 1 1 1c0 1.25.2 2.45.57 3.57a1 1 0 0 1-.25 1z"/></svg>
  <div class="abs phone-num">123-456-7890</div>

  <nav class="abs nav">
    <a class="active">HOME</a><span class="sep">|</span>
    <a>How We Work</a><span class="sep">|</span>
    <a>BASKET</a><span class="sep">|</span>
    <a>CONTACT US</a>
  </nav>

  <div class="abs hero" role="img" aria-label="Wooden raised garden bed planted with strawberry leaves"></div>
  <svg class="abs hero-arrow" style="left:24px" width="24" height="42" viewBox="0 0 24 42"><polyline points="22,2 3,21 22,40" fill="none" stroke="#fff" stroke-width="2"/></svg>
  <svg class="abs hero-arrow" style="left:973px" width="24" height="42" viewBox="0 0 24 42"><polyline points="2,2 21,21 2,40" fill="none" stroke="#fff" stroke-width="2"/></svg>
  <div class="abs caption">We Are Online-only Garden Installation Company</div>

  <h2 class="abs section-title">Select Size Of The Garden</h2>
  <div class="abs title-rule"></div>

  <div class="abs card" style="left:68px">
    <div class="card-photo" role="img" aria-label="Small raised wooden garden bed with vegetables"></div>
    <div class="card-text">Lorem Ispum is the Dummy Text</div>
    <div class="card-bar"><span class="size">Size : 4’ X 4’</span><span class="price">$175.00</span><span class="buy"><svg width="12" height="10" viewBox="0 0 12 10"><path d="M0 1h2l2 6h6l1.5-4.5H3" fill="none" stroke="#fff" stroke-width="1.3"/><circle cx="5" cy="9" r="1" fill="#fff"/><circle cx="9" cy="9" r="1" fill="#fff"/></svg>Buy Now</span></div>
  </div>
  <div class="abs card" style="left:371px">
    <div class="card-photo" role="img" aria-label="Medium raised wooden garden bed with vegetables"></div>
    <div class="card-bar"><span class="size">Size : 8’ X 4’</span><span class="price">$275.00</span><span class="buy"><svg width="12" height="10" viewBox="0 0 12 10"><path d="M0 1h2l2 6h6l1.5-4.5H3" fill="none" stroke="#fff" stroke-width="1.3"/><circle cx="5" cy="9" r="1" fill="#fff"/><circle cx="9" cy="9" r="1" fill="#fff"/></svg>Buy Now</span></div>
  </div>
  <div class="abs card" style="left:673px">
    <div class="card-photo" role="img" aria-label="Large raised wooden garden bed with vegetables"></div>
    <div class="card-bar"><span class="size">Size : 12’ X 4’</span><span class="price">$375.00</span><span class="buy"><svg width="12" height="10" viewBox="0 0 12 10"><path d="M0 1h2l2 6h6l1.5-4.5H3" fill="none" stroke="#fff" stroke-width="1.3"/><circle cx="5" cy="9" r="1" fill="#fff"/><circle cx="9" cy="9" r="1" fill="#fff"/></svg>Buy Now</span></div>
  </div>

  <footer class="abs footer" role="img" aria-label="Dark background photo of freshly pulled carrots"></footer>

  <div class="abs f-head" style="top:964px;left:70px">About Us</div>
  <div class="abs f-rule" style="top:991px;left:70px;width:214px"></div>
  <p class="abs f-body" style="top:1000px;left:70px;width:220px">Lorem ipsum dolor rrsit amet, consectetuer adipiscing efdflit, sed diarm nonummy nibh euismod tincidunt ut laoreet dolona aliquam erat volutpat. Ut wisi enim ad mim ventirrm, quis nostrud exerci tation ullamcer surscipit lo Duis autem vel eum iriure drelor iendrerit in vulputate velit esse molestie conquat, vel illum dolore eu feugiat nulla.</p>

  <div class="abs f-head" style="top:964px;left:330px">Contact Info</div>
  <div class="abs f-rule" style="top:991px;left:330px;width:182px"></div>
  <div class="abs f-line" style="top:1001px;left:329px"><svg width="10" height="10" viewBox="0 0 24 24"><path fill="#4caf50" d="M6.6 10.8a15.1 15.1 0 0 0 6.6 6.6l2.2-2.2a1 1 0 0 1 1-.25 11.4 11.4 0 0 0 3.6.57 1 1 0 0 1 1 1V20a1 1 0 0 1-1 1A17 17 0 0 1 3 4a1 1 0 0 1 1-1h3.5a1 1 0 0 1 1 1c0 1.25.2 2.45.57 3.57a1 1 0 0 1-.25 1z"/></svg>123 - 456 - 7890</div>
  <div class="abs f-line" style="top:1032px;left:326px"><svg width="12" height="9" viewBox="0 0 12 9"><rect x=".5" y=".5" width="11" height="8" fill="none" stroke="#4caf50"/><polyline points=".5,.5 6,5 11.5,.5" fill="none" stroke="#4caf50"/></svg>info@pebblebrookplots.com</div>

  <div class="abs f-head" style="top:1069px;left:327px">Social Media</div>
  <div class="abs f-rule" style="top:1095px;left:327px;width:172px"></div>
  <div class="abs social"><span style="background:#3b5ba0"></span><span style="background:#1f82c0"></span><span style="background:#d8453a"></span><span style="background:#c8302a"></span></div>

  <div class="abs f-head" style="top:964px;left:556px">Newsletter Signup</div>
  <div class="abs f-rule" style="top:991px;left:556px;width:160px"></div>
  <p class="abs f-body" style="top:998px;left:556px;width:180px;font-size:10.8px;line-height:15.5px">Get latest updates by entering your email address</p>
  <div class="abs input">Email Address</div>
  <div class="abs subscribe">SUBSCRIBE</div>

  <div class="abs f-brand">PEBBLEBROOK PLOTS</div>

  <div class="abs bottom">
    <div class="abs copy">Copyright © 2017 PEBBLEBROOK PLOTS. All Rights Reserved.</div>
    <div class="abs accept">We Accept</div>
    <div class="abs cards"><span>Cardo</span><span>Duomark</span><span>Paystream</span></div>
  </div>
</div>
</body>
</html>
```